Residential Remodeling Contractor needs updated business card

I need a new design for my business card.
Name of the company is Ridgefell Construction. I need a card that commands presence, strength, integrity. I have been in business for 28 years. I am a Residential Remodeling Contractor that covers all aspects of a residential remodel and build.

```html
<!DOCTYPE html>
<html lang="en">
<head>
<meta charset="utf-8">
<title>Ridgefell Construction – Business Card</title>
<link rel="stylesheet" href="https://fonts.googleapis.com/css2?family=Noto+Serif:wght@700&family=Arimo:wght@400&display=swap">
<style>
  :root {
    --navy: #183d7a;
    --ink: #333333;
    --paper: #ffffff;
    --backdrop: #9a9a9a;
  }
  * { margin: 0; padding: 0; box-sizing: border-box; }
  html, body { width: 1200px; height: 1059px; overflow: hidden; }
  body { background: var(--backdrop); position: relative; font-family: "Arimo", Arial, sans-serif; }

  .card { position: absolute; border-radius: 18px; overflow: hidden; }
  .card-front { left: 256px; top: 89px; width: 688px; height: 391px; background: var(--paper); }
  .card-back { left: 253px; top: 569px; width: 694px; height: 395px; background: var(--navy); }

  .brand {
    position: absolute;
    font-family: "Noto Serif", Georgia, serif;
    font-weight: 700;
    text-transform: uppercase;
    line-height: 1.05;
  }
  .card-front .brand {
    right: 32px; top: 62px; text-align: right;
    color: var(--navy); font-size: 27px; letter-spacing: 0.5px;
  }
  .card-back .brand {
    left: 0; right: 0; top: 158px; text-align: center;
    color: var(--paper); font-size: 46px; letter-spacing: 1px;
  }

  .person { position: absolute; left: 31px; top: 190px; }
  .person-name {
    font-family: "Noto Serif", Georgia, serif; font-weight: 700;
    font-size: 27px; color: var(--navy); line-height: 1.1; letter-spacing: 0.2px;
  }
  .person-role { font-size: 16px; color: var(--ink); margin-top: 2px; }

  .divider { position: absolute; left: 31px; right: 31px; top: 259px; height: 1px; background: var(--navy); }

  .contacts { position: absolute; left: 31px; top: 282px; list-style: none; }
  .contacts li { display: flex; align-items: center; height: 27px; font-size: 17px; color: var(--ink); }
  .contacts svg { width: 13px; height: 13px; margin-right: 7px; flex: none; }

  .address {
    position: absolute; right: 32px; top: 312px; text-align: right;
    font-size: 17px; line-height: 22px; color: var(--ink); font-style: normal;
  }
</style>
</head>
<body>
  <section class="card card-front">
    <div class="brand">Ridgefell<br>Construction</div>

    <div class="person">
      <div class="person-name">DANIEL WESTBROOK</div>
      <div class="person-role">Owner &amp; Manager</div>
    </div>

    <div class="divider"></div>

    <ul class="contacts">
      <li>
        <svg viewBox="0 0 14 14" aria-hidden="true"><path fill="#183d7a" d="M1 5c0-2 3-3 6-3s6 1 6 3v1h-3V5H4v1H1zM3 7h8l1 5H2z"/></svg>
        555 014 2876
      </li>
      <li>
        <svg viewBox="0 0 14 14" aria-hidden="true"><path fill="#183d7a" d="M1 5l6-4 6 4v8H1z"/><path fill="none" stroke="#fff" stroke-width="1" d="M1.5 5.5L7 9l5.5-3.5"/></svg>
        info@ridgefellconstruction.com
      </li>
      <li>
        <svg viewBox="0 0 14 14" aria-hidden="true"><circle cx="7" cy="7" r="6" fill="#183d7a"/><path fill="#fff" d="M4 4h3v2H5zM8 8h3l-1 3H8z"/></svg>
        www.ridgefellconstruction.com
      </li>
    </ul>

    <address class="address">
      P.O. Box&nbsp; Street Name<br>
      Country Name AB, A5B 521
    </address>
  </section>

  <section class="card card-back">
    <div class="brand">Ridgefell<br>Construction</div>
  </section>
</body>
</html>
```